I am a general contractor in Portland, Or. I would like a clean and simple design layout, maybe using the "didot" font, blue and dark bronze in colors are preferred. On one side of the card, it would be nice to have a logo(attached photo) and business name(KTW Construction). I don't need my job title on the card, just some thing along the lines of "gordon pike, general contractor". Thanks much.

Target Market(s)

Adults from 30-55 years old. Middle to upper class.

Industry/Entity Type

Contractor

Contact Information for Business Card

KTW Construction
Gordon L. Pike
2843 NE 71st Ave.
Portland, Or. 97288
541.555.0187

Font styles to use
Other font styles liked:
• didot

Colors
3277b5
7f7f7f

Requirements
Should not have
• Too much going on.

```html
<!DOCTYPE html>
<html lang="en">
<head>
<meta charset="utf-8">
<title>KTW Construction – Business Card</title>
<link rel="stylesheet" href="https://fonts.googleapis.com/css2?family=Exo+2:wght@300;400;700&display=swap">
<style>
  :root {
    --backdrop: #e6e7ea;
    --card-top: #ffffff;
    --card-bottom: #e9eaec;
    --navy: #2a3a8a;
    --blue: #3277b5;
    --band-dark: #2b3487;
    --band-light: #3a4fa8;
    --rule: #3a3a3c;
    --ink-grey: #55575c;
    --white: #ffffff;
  }
  * { margin: 0; padding: 0; box-sizing: border-box; }
  html, body { width: 1200px; height: 900px; overflow: hidden; }
  body {
    background: var(--backdrop);
    font-family: "Exo 2", sans-serif;
    position: relative;
  }
  .card {
    position: absolute;
    left: 250px;
    width: 1000px; height: 570px;
    transform: scale(0.7);
    transform-origin: top left;
    border-radius: 48px;
    overflow: hidden;
    background: linear-gradient(160deg, var(--card-top) 30%, var(--card-bottom) 100%);
    box-shadow: 0 10px 30px rgba(0,0,0,0.12);
  }
  .card-front { top: 40px; }
  .card-back { top: 461px; }
  .wave { position: absolute; inset: 0; width: 1000px; height: 570px; }
  .brand {
    position: absolute; left: 62px; top: 40px;
    display: flex; align-items: center; gap: 28px;
  }
  .brand-dot {
    width: 110px; height: 110px; border-radius: 50%;
    background: var(--blue);
  }
  .brand-name {
    color: var(--navy);
    font-weight: 700;
    font-size: 56px;
    line-height: 0.98;
  }
  .card-back .brand {
    left: 0; right: 0; top: 0; bottom: 0;
    justify-content: center;
    gap: 40px;
  }
  .card-back .brand-dot { width: 160px; height: 160px; }
  .card-back .brand-name { font-size: 80px; }
  .person { position: absolute; left: 62px; top: 182px; color: var(--ink-grey); }
  .person-name { font-size: 27px; font-weight: 400; letter-spacing: 3px; text-transform: uppercase; }
  .person-role { font-size: 18px; font-weight: 300; letter-spacing: 2px; text-transform: uppercase; margin-top: 2px; }
  .address {
    position: absolute; left: 40px; top: 298px;
    color: var(--white); font-size: 22px; font-weight: 300; letter-spacing: 1px; line-height: 1.45;
  }
  .contacts {
    position: absolute; right: 44px; top: 420px;
    list-style: none; color: var(--white);
    font-size: 19px; font-weight: 300; letter-spacing: 1px;
  }
  .contacts li { display: flex; justify-content: flex-end; align-items: center; gap: 12px; height: 27px; }
  .contacts svg { width: 18px; height: 18px; fill: none; stroke: var(--white); stroke-width: 1.8; }
</style>
</head>
<body>
  <div class="card card-front">
    <svg class="wave" viewBox="0 0 1000 570" aria-hidden="true">
      <defs>
        <linearGradient id="bandFill" x1="0" y1="0" x2="1" y2="1">
          <stop offset="0" stop-color="#2b3487"/>
          <stop offset="1" stop-color="#3a4fa8"/>
        </linearGradient>
      </defs>
      <path d="M0,252 C300,246 540,346 1000,392 L1000,570 L0,570 Z" fill="#3a3a3c"/>
      <path d="M0,262 C300,256 540,356 1000,402 L1000,570 L0,570 Z" fill="#ffffff"/>
      <path d="M0,270 C300,264 540,364 1000,410 L1000,570 L0,570 Z" fill="url(#bandFill)"/>
    </svg>

    <div class="brand">
      <div class="brand-dot"></div>
      <div class="brand-name">KTW<br>Construction</div>
    </div>

    <div class="person">
      <p class="person-name">Gordon Pike</p>
      <p class="person-role">General Contractor</p>
    </div>

    <p class="address">2843 NE 71st Ave.<br>Portland, Or. 97288</p>

    <ul class="contacts">
      <li>541.555.0187
        <svg viewBox="0 0 20 20"><path d="M5 2 L8 2 L9 6 L7 8 C8 11 9 12 12 13 L14 11 L18 12 L18 15 C18 17 16 18 14 18 C8 17 3 12 2 6 C2 4 3 2 5 2 Z"/></svg>
      </li>
      <li>541.555.0188
        <svg viewBox="0 0 20 20"><rect x="6" y="2" width="8" height="16" rx="1.5"/><line x1="9" y1="15.5" x2="11" y2="15.5"/></svg>
      </li>
      <li>541.555.0189
        <svg viewBox="0 0 20 20"><rect x="3" y="8" width="14" height="9"/><rect x="6" y="3" width="8" height="5"/><line x1="6" y1="12" x2="14" y2="12"/></svg>
      </li>
      <li>gordon@ktwbuild.com
        <svg viewBox="0 0 20 20"><rect x="2" y="5" width="16" height="11"/><polyline points="2,5 10,11 18,5"/></svg>
      </li>
      <li>www.ktwbuild.com
        <svg viewBox="0 0 20 20"><circle cx="10" cy="10" r="8"/><ellipse cx="10" cy="10" rx="3.5" ry="8"/><line x1="2" y1="10" x2="18" y2="10"/></svg>
      </li>
    </ul>
  </div>

  <div class="card card-back">
    <div class="brand">
      <div class="brand-dot"></div>
      <div class="brand-name">KTW<br>Construction</div>
    </div>
  </div>
</body>
</html>
```